KAJU Freightways #ALLKAJU Business Cards & Letterhead

I am looking to business cards designed for our organization. We are currently undergoing a small re-branding that is taking place. Our organization is called KAJU Freightways and we are headquartered in Phoenix, AZ. We primarily provide transportation and logistics services to the Marlow Parcel Bureau who is our largest customer. I would like to see a design that incorporates name, title, contact info, website, and address (this will be different depending on the employee). I would also like to see some color on the business card using our logo colors or a variation. I would like our logo on the back of the business card with the website displayed. The final design should communicate that we are a next generation transportation operate that focuses on being driver-first, customer-centric, innovative, and sustainable.We would also like our #ALLKAJU catch phrase incorporated as well.

Target Market(s)

Transportation & Logistics

Industry/Entity Type

Trucking Company

Contact Information for Business Card

-First and Last Name
-Position Title
-Contact Phone
-Contact Email
-Physical Address

Font styles to use
Serif

Colors

Designer to choose colors to be used in the design.

Requirements
Must have
• -KAJU logo prominently displayed
• -#ALLKAJU catch phrase used
• -Some amount of color, design gradient, etc.
• -Logo on the back with website listed (https://www.kajufreightco.example)

```html
<!DOCTYPE html>
<html lang="en">
<head>
<meta charset="UTF-8">
<title>KAJU Freightways — Business Cards</title>
<link rel="stylesheet" href="https://fonts.googleapis.com/css2?family=Montserrat:wght@300;400;700;800&display=swap">
<style>
  :root {
    --stage: #1d2124;
    --teal-deep: #0f3442;
    --teal: #15414f;
    --grey: #8f9090;
    --grey-light: #9a9b9b;
    --green: #6cc33a;
    --white: #ffffff;
    --muted: #5f7c86;
  }
  * { margin: 0; padding: 0; box-sizing: border-box; }
  html, body {
    width: 1200px; height: 900px; overflow: hidden;
    background: var(--stage);
    font-family: "Montserrat", sans-serif;
  }
  .stage {
    position: relative; width: 1200px; height: 900px;
    display: flex; align-items: center; justify-content: center; gap: 60px;
  }
  .card {
    position: relative; width: 520px; height: 297px; overflow: hidden;
    box-shadow: 0 18px 40px rgba(0,0,0,.45);
  }

  /* Front card */
  .card--front { background: var(--teal-deep); }
  .front__top {
    position: absolute; left: 0; top: 0; width: 100%; height: 150px;
    background: linear-gradient(180deg, var(--grey-light), var(--grey));
    border-bottom: 3px solid var(--green);
  }
  .brand-mark {
    position: absolute; left: 26px; top: 38px;
    display: flex; align-items: center; gap: 12px;
  }
  .brand-mark__dot {
    width: 26px; height: 26px; border-radius: 50%;
    border: 4px solid var(--green);
  }
  .brand-mark__name {
    font-weight: 800; font-size: 50px; letter-spacing: 1px;
    color: var(--teal-deep); line-height: 1;
  }
  .front__contact {
    position: absolute; left: 26px; top: 168px; color: var(--muted);
  }
  .person__name {
    font-weight: 700; font-size: 16px; letter-spacing: .5px;
    color: var(--white); text-transform: uppercase;
  }
  .person__title {
    font-weight: 400; font-size: 12px; color: #c9d3d6; margin-bottom: 10px;
  }
  .contact-list { list-style: none; font-size: 11.5px; font-weight: 300; }
  .contact-list li { display: flex; align-items: center; gap: 8px; height: 17px; }
  .contact-list svg { width: 11px; height: 11px; flex: none; }
  .front__side {
    position: absolute; right: 24px; bottom: 22px; text-align: right;
  }
  .hashtag {
    font-weight: 400; font-size: 17px; letter-spacing: 1px;
    color: var(--green); margin-bottom: 8px;
  }
  .address {
    font-weight: 300; font-size: 13px; line-height: 1.35; color: var(--muted);
  }

  /* Back card */
  .card--back {
    background: radial-gradient(ellipse at 55% 40%, #1a4756 0%, var(--teal-deep) 75%);
  }
  .back__logo {
    position: absolute; left: 0; right: 0; top: 72px; text-align: center;
    font-weight: 800; font-size: 84px; letter-spacing: 2px;
    color: var(--white); line-height: 1;
  }
  .back__tagline {
    position: absolute; left: 0; right: 0; top: 166px; text-align: center;
    font-weight: 400; font-size: 15px; letter-spacing: 3px; color: var(--white);
  }
  .back__web {
    position: absolute; left: 0; right: 0; top: 218px;
    display: flex; align-items: center; gap: 12px;
    font-weight: 300; font-size: 14px; color: var(--white);
  }
  .back__web .rule { flex: 1; height: 1px; background: var(--green); }
  .back__web strong { font-weight: 700; color: var(--green); }
</style>
</head>
<body>
<main class="stage">

  <section class="card card--front" aria-label="Business card front">
    <div class="front__top">
      <div class="brand-mark">
        <span class="brand-mark__dot"></span>
        <span class="brand-mark__name">KAJU</span>
      </div>
    </div>

    <div class="front__contact">
      <p class="person__name">Dana Whitlock</p>
      <p class="person__title">Chairman &amp; CEO</p>
      <ul class="contact-list">
        <li>
          <svg viewBox="0 0 12 12"><circle cx="6" cy="6" r="5" fill="none" stroke="#6cc33a" stroke-width="1.2"/><path d="M4 3.5l1 1.2-.6.8c.4.8 1 1.4 1.8 1.8l.8-.6 1.2 1-.6 1c-2.2-.3-3.9-2-4.2-4.2z" fill="#6cc33a"/></svg>
          555-014-2290
        </li>
        <li>
          <svg viewBox="0 0 12 12"><rect x="1" y="2.5" width="10" height="7" fill="none" stroke="#6cc33a" stroke-width="1.2"/><path d="M1 2.5l5 4 5-4" fill="none" stroke="#6cc33a" stroke-width="1.2"/></svg>
          info@kajufreightco.example
        </li>
        <li>
          <svg viewBox="0 0 12 12"><circle cx="6" cy="6" r="5" fill="none" stroke="#6cc33a" stroke-width="1.2"/><path d="M1 6h10M6 1c-2 2.5-2 7.5 0 10M6 1c2 2.5 2 7.5 0 10" fill="none" stroke="#6cc33a" stroke-width="1"/></svg>
          www.kajufreightco.example
        </li>
      </ul>
    </div>

    <div class="front__side">
      <p class="hashtag">#ALLKAJU</p>
      <p class="address">4170 Desert Ridge<br>Parkway, Glendale, AZ 85310</p>
    </div>
  </section>

  <section class="card card--back" aria-label="Business card back">
    <p class="back__logo">KAJU</p>
    <p class="back__tagline">FREIGHTWAYS</p>
    <p class="back__web">
      <span class="rule"></span>
      <span>www.<strong>kajufreightco</strong>.example</span>
      <span class="rule"></span>
    </p>
  </section>

</main>
</body>
</html>
```